Brightmill Data Works

Our company is about IT hardwares and IT solutions. IT hardware such as PC, RAMS, storage and servers. IT solutions such as project management, BA. We are also selling new technology too.

Target Market(s)

Consumer, Small to Medium Business, Corporate

Requirements
Must have
• The business card must have the following:
• Name:
• Title:
• Contact Number:
• Email address:
• Website:
• Color: Must match the logo color upgrade

```html
<!DOCTYPE html>
<html lang="en">
<head>
<meta charset="utf-8">
<title>Brightmill Data Works – Business Card</title>
<link href="https://fonts.googleapis.com/css2?family=Lato:wght@400;700;900&display=swap" rel="stylesheet">
<style>
  :root {
    --backdrop: #1a1a1a;
    --card-dark: #232323;
    --card-light: #ffffff;
    --ink: #3b3b3d;
    --ink-soft: #2a2a2a;
    --amber: #e09a3a;
    --band: #1f1f1f;
    --on-dark: #f2f2f2;
  }
  * { margin: 0; padding: 0; box-sizing: border-box; }
  html, body { width: 1200px; height: 912px; overflow: hidden; }
  body {
    background: var(--backdrop);
    font-family: "Lato", sans-serif;
    position: relative;
  }
  .card {
    position: absolute;
    width: 560px;
    height: 320px;
    border-radius: 2px;
    overflow: hidden;
    box-shadow: 0 18px 40px rgba(0,0,0,.55);
  }
  /* Front side */
  .card-front {
    left: 70px; top: 80px;
    background: linear-gradient(160deg, #2c2c2c, var(--card-dark) 60%, #1c1c1c);
  }
  .card-front .brand {
    position: absolute; left: 0; right: 0; top: 118px;
    display: flex; align-items: center; justify-content: center; gap: 12px;
  }
  .brand-mark { width: 16px; height: 16px; background: var(--amber); flex: none; }
  .card-front .brand-name {
    font-weight: 900; font-size: 30px; letter-spacing: 1px;
    color: var(--on-dark); text-transform: uppercase;
  }
  .card-front .web {
    position: absolute; left: 0; right: 0; bottom: 42px;
    text-align: center; color: var(--on-dark); font-size: 14px; letter-spacing: .5px;
  }
  /* Back side */
  .card-back {
    left: 570px; top: 480px;
    background: var(--card-light);
  }
  .card-back .swoosh { position: absolute; left: 0; top: 0; }
  .card-back .brand {
    position: absolute; left: 34px; top: 70px;
    display: flex; align-items: center; gap: 10px;
  }
  .card-back .brand-mark { width: 14px; height: 14px; }
  .card-back .brand-name {
    font-weight: 900; font-size: 19px; letter-spacing: .3px;
    color: var(--ink); text-transform: uppercase;
  }
  .person { position: absolute; left: 34px; top: 128px; }
  .person-name { color: var(--amber); font-weight: 700; font-size: 24px; }
  .person-title { color: var(--ink-soft); font-size: 15px; margin-top: 2px; }
  .contact {
    position: absolute; right: 28px; top: 48px;
    color: var(--ink-soft); font-size: 13px; line-height: 1.45;
  }
  .contact .address { margin-bottom: 8px; }
  .contact-row { display: flex; align-items: center; gap: 8px; }
  .contact-row svg { width: 12px; height: 12px; flex: none; }
  .card-back .web {
    position: absolute; left: 34px; bottom: 16px;
    color: var(--on-dark); font-size: 14px; letter-spacing: .5px;
  }
</style>
</head>
<body>

<section class="card card-front">
  <div class="brand">
    <span class="brand-mark"></span>
    <span class="brand-name">Brightmill Data Works</span>
  </div>
  <p class="web">www.brightmilldata.com</p>
</section>

<section class="card card-back">
  <svg class="swoosh" width="560" height="320" viewBox="0 0 560 320">
    <path d="M0 236 C 200 252, 420 226, 560 168 L560 320 L0 320 Z" fill="var(--amber)"/>
    <path d="M0 250 C 210 262, 430 236, 560 180 L560 320 L0 320 Z" fill="var(--card-light)"/>
    <path d="M0 256 C 210 266, 430 242, 560 186 L560 320 L0 320 Z" fill="var(--band)"/>
  </svg>

  <div class="brand">
    <span class="brand-mark"></span>
    <span class="brand-name">Brightmill Data Works</span>
  </div>

  <div class="person">
    <p class="person-name">Daniel Hartley</p>
    <p class="person-title">Manager</p>
  </div>

  <div class="contact">
    <p class="address">418 Alder Court<br>Austin, TX 78702</p>
    <p class="contact-row">
      <svg viewBox="0 0 12 12"><path d="M2 1l2 0 1 3-1.5 1a6 6 0 0 0 3 3L7.5 6.5l3 1v2A1.5 1.5 0 0 1 9 11 8.5 8.5 0 0 1 1 3 1.5 1.5 0 0 1 2 1z" fill="var(--amber)"/></svg>
      512 555 0142
    </p>
    <p class="contact-row">
      <svg viewBox="0 0 12 12"><rect x="3" y="1" width="6" height="3" fill="var(--amber)"/><rect x="1" y="4.5" width="10" height="4.5" rx="1" fill="var(--amber)"/><rect x="3" y="7.5" width="6" height="3.5" fill="var(--amber)" stroke="#fff" stroke-width=".8"/></svg>
      512 555 0143
    </p>
    <p class="contact-row">
      <svg viewBox="0 0 12 12"><rect x="1" y="2.5" width="10" height="7" fill="var(--amber)"/><path d="M1 2.5l5 4 5-4" fill="none" stroke="#fff" stroke-width="1"/></svg>
      info@brightmilldata.com
    </p>
  </div>

  <p class="web">www.brightmilldata.com</p>
</section>

</body>
</html>
```